Business price tag design for Furniture Business

Hello,

I have developed a tag for a home furniture business and need 1 more creative template. Please see attachment. I need the template to be very appealing.

Requirements:

1.Tag dimensions needs to be about the same as attached tag.
2. Tag design needs to be suitable for a home furniture business.
3. Tag needs to have locations for the following: Item Title, Now Price, Was Price, Product Number.
4. "The black shape at the bottom of attached tag could be removed.

I have no requirements on colors, but something professional is needed, preferably white background to reduce print ink consumption.

Please see attachment for clarification.

Industry/Entity Type

Retail

Font styles to use
Serif
Sans Serif

Requirements
Must have
• Please see Project Description.
Nice to have

```html
<!DOCTYPE html>
<html lang="en">
<head>
<meta charset="utf-8">
<title>Furniture Price Tag</title>
<link href="https://fonts.googleapis.com/css2?family=Arimo:wght@400&display=swap" rel="stylesheet">
<style>
  :root {
    --leaf: #8cc63f;
    --walnut: #8b5a36;
    --paper: #ffffff;
  }
  html, body {
    margin: 0;
    padding: 0;
    width: 1200px;
    height: 2308px;
    overflow: hidden;
    background: var(--paper);
  }
  .tag {
    position: relative;
    width: 1200px;
    height: 2308px;
    font-family: "Arimo", Arial, sans-serif;
    font-weight: 400;
  }
  .tag-frame {
    position: absolute;
    inset: 6px;
    border: 14px solid var(--leaf);
  }
  .tag-inner {
    position: absolute;
    left: 48px;
    top: 48px;
    width: 1104px;
    height: 2200px;
    box-sizing: border-box;
    border: 7px solid var(--walnut);
    border-radius: 100px;
  }
  .field {
    position: absolute;
    left: 432px;
    width: 608px;
    box-sizing: border-box;
    border: 7px solid var(--leaf);
    background: var(--paper);
  }
  .field span {
    position: absolute;
    display: block;
    line-height: 1;
    white-space: nowrap;
  }
  .label { color: var(--leaf); }
  .value { color: var(--walnut); }

  .store { top: 80px; height: 528px; }
  .store-name {
    left: 84px; top: 56px;
    font-size: 96px;
    line-height: 128px !important;
    color: var(--leaf);
    white-space: normal !important;
  }

  .item { top: 640px; height: 480px; }
  .item .label { left: 112px; top: 36px; font-size: 64px; }
  .item .value { left: 112px; top: 164px; font-size: 80px; line-height: 112px !important; white-space: normal !important; }

  .product { top: 1152px; height: 220px; }
  .product .label { left: 108px; top: 36px; font-size: 52px; }
  .product .value { left: 108px; top: 116px; font-size: 60px; }

  .now { top: 1400px; height: 480px; }
  .now .label { left: 108px; top: 28px; font-size: 80px; }
  .now .value { left: 108px; top: 196px; font-size: 168px; }

  .was { top: 1912px; height: 348px; }
  .was .label { left: 108px; top: 16px; font-size: 80px; }
  .was .value { left: 108px; top: 144px; font-size: 112px; }
</style>
</head>
<body>
  <div class="tag">
    <div class="tag-frame"></div>
    <div class="tag-inner"></div>

    <div class="field store">
      <span class="store-name">Oakline<br>Furniture<br>Depot</span>
    </div>

    <div class="field item">
      <span class="label">Item Title</span>
      <span class="value">Black<br>King Bed</span>
    </div>

    <div class="field product">
      <span class="label">Product Number</span>
      <span class="value">B9999</span>
    </div>

    <div class="field now">
      <span class="label">Now Price</span>
      <span class="value">$555</span>
    </div>

    <div class="field was">
      <span class="label">Was Price</span>
      <span class="value">$666</span>
    </div>
  </div>
</body>
</html>
```